Corvina Dental personal information forms

We are a Dental Practice that require an update to our information forms, there are 3 versions of it.
I will attach our old ones, we need to keep the same information on there, we just want them to look better and use our current logo and colours.
Our website is www.corvinadental.net
Our facebook is www.friendspage.net/corvinadentalbelmorewalk/
..................................................................................................

Target Market(s)

Everyone, easy to read

Industry/Entity Type

Dental Clinic

Colors
0692cd
34a6d7
cee9f5
ffffff
0255a3
3276b5

Requirements
Must have
• Logo
• Our colours
• same information as the uploaded versions
Should not have
• any other colour besides the blues, black and white

```html
<!DOCTYPE html>
<html lang="en">
<head>
<meta charset="utf-8">
<title>Corvina Dental – Patient Information Forms</title>
<link href="https://fonts.googleapis.com/css2?family=Open+Sans:ital,wght@0,400;0,600;0,700;1,400;1,600&display=swap" rel="stylesheet">
<style>
:root{
  --blue-deep:#0255a3;
  --blue-mid:#3276b5;
  --blue-bright:#0692cd;
  --blue-sky:#34a6d7;
  --blue-pale:#cee9f5;
  --white:#ffffff;
  --ink:#1a1a1a;
  --stage:#f1f1f1;
}
*{box-sizing:border-box;margin:0;padding:0}
html,body{width:1200px;height:1200px;overflow:hidden}
body{background:var(--stage);font-family:"Open Sans",Arial,sans-serif;color:var(--ink);position:relative;-webkit-font-smoothing:antialiased;-moz-osx-font-smoothing:grayscale}

.brand-name{position:absolute;right:110px;top:170px;color:var(--blue-deep);font-weight:600;font-size:84px;line-height:1;letter-spacing:0;white-space:nowrap}

.form-set{position:absolute;left:40px;top:380px;display:flex;gap:30px}
.form{width:360px;height:510px;background:var(--white);padding:18px 16px;font-size:6.6px;line-height:1.45;box-shadow:0 6px 18px rgba(0,0,0,.12);overflow:hidden;position:relative}
.form__head{display:flex;justify-content:space-between;align-items:flex-start;gap:10px}
.form__head--logo-only{justify-content:flex-end}
.form__name{color:var(--blue-deep);font-weight:600;font-size:13px;line-height:1;white-space:nowrap}
.form__doctors{color:var(--blue-deep);font-weight:600;margin-top:10px}
.form__head .form__doctors{margin-top:0}
.form__welcome{font-style:italic;font-weight:600;margin-top:10px}
.form__intro{font-style:italic;margin-top:6px}
.q{color:var(--blue-deep);font-weight:600;margin-top:9px}
.answer{color:var(--blue-deep);display:flex;gap:8px;align-items:center;margin-top:2px}
.radio{display:inline-block;width:8px;height:8px;border-radius:50%;background:var(--blue-pale);vertical-align:middle}
.radio--line{background:none;border:1px solid var(--blue-sky)}
.rule{border-bottom:1px solid #555;height:10px;margin-bottom:2px}
.band{background:var(--blue-deep);color:var(--white);font-weight:700;text-align:center;padding:3px;margin:8px -16px 6px;text-transform:uppercase;font-size:6.4px}
.band--sky{background:var(--blue-sky);margin:8px 0 0}
.band--bright{background:var(--blue-bright)}
.band--plain{text-transform:none}
.conditions{display:grid;grid-template-columns:repeat(2,1fr);gap:1px 10px}
.conditions--three{grid-template-columns:repeat(3,1fr)}
.conditions li{list-style:none;display:flex;align-items:center;gap:5px}
.two-col{display:grid;grid-template-columns:1fr 1fr;gap:10px}
.sign{font-weight:700;margin-top:10px}
.declare{font-style:italic;font-weight:600;margin-top:8px}
.info-table{border:1px solid var(--blue-sky);color:var(--blue-bright)}
.info-table--fill{background:var(--blue-pale)}
.info-table .row{display:grid;grid-template-columns:62px 1fr;border-top:1px solid var(--blue-sky);min-height:10px}
.info-table .row:first-child{border-top:none}
.info-table .row span:first-child{border-right:1px solid var(--blue-sky);padding:0 3px}
.info-table .row span:last-child{padding:0 3px;text-align:right}
.info-table .title{padding:1px 3px}
.info-table .title--ruled{border-top:1px solid var(--blue-sky)}
.plain-fields .field{display:flex;gap:4px;margin-top:3px}
.plain-fields .field i{flex:1;border-bottom:1px solid #555;font-style:normal}
.insurance{margin-top:6px}
.note{font-style:italic;font-weight:700;margin-top:8px}
.split{display:grid;grid-template-columns:1fr 1fr;gap:8px}
</style>
</head>
<body>

<div class="brand-name">Corvina Dental</div>

<div class="form-set">

  <section class="form form--history">
    <div class="form__head form__head--logo-only"><div class="form__name">Corvina Dental</div></div>
    <p class="form__doctors">Dr. Stefan Koralis &amp; Dr. Henry Ashford<br>Dental Surgeons</p>
    <p class="form__welcome">Welcome Back To Our Practice!</p>
    <p class="form__intro">This information is confidential and is necessary to enable us to offer you The Best Possible Care. It is now mandatory to have written updated medical history every 2 years and we would appreciate your time in thoroughly completing this form.</p>
    <p class="q">Are you currently or have any prescribed medication or dietary supplements in the last 12 months?</p>
    <div class="answer">Yes <span class="radio"></span> No <span class="radio"></span> (If yes, please list below)</div>
    <div class="rule"></div>
    <p class="q">Allergies / Reactions?</p>
    <div class="answer">Yes <span class="radio"></span> No <span class="radio"></span> (If yes, please list below)</div>
    <div class="rule"></div>
    <div class="band band--plain">Have you ever had or are you suffering from any of the following? Please tick any that apply:</div>
    <ul class="conditions">
      <li><span class="radio"></span>Rheumatic fever</li><li><span class="radio"></span>Diabetes</li>
      <li><span class="radio"></span>Epilepsy</li><li><span class="radio"></span>Kidney Disease</li>
      <li><span class="radio"></span>Asthma</li><li><span class="radio"></span>Heart Attack</li>
      <li><span class="radio"></span>Tuberculosis</li><li><span class="radio"></span>High Blood Pressure</li>
      <li><span class="radio"></span>Radiation Therapy</li><li><span class="radio"></span>Bleeding problems</li>
      <li><span class="radio"></span>Dizziness, fainting</li><li><span class="radio"></span>Artificial joints</li>
      <li><span class="radio"></span>Hepatitis A B or C</li><li><span class="radio"></span>Respiratory problems</li>
      <li><span class="radio"></span>Recent eye surgery</li>
    </ul>
    <div class="two-col">
      <div>
        <p class="q">Do you have any disease, condition or problem not listed above?</p>
        <div class="answer">Yes <span class="radio"></span> No <span class="radio"></span></div>
        <div class="rule"></div>
        <p class="q">For Women: Are you pregnant?</p>
        <div class="answer">Yes <span class="radio"></span> No <span class="radio"></span> (If yes, how many months)</div>
        <div class="rule"></div>
      </div>
      <div>
        <p class="q">Have you had surgery in the last 2 years?</p>
        <div class="answer">Yes <span class="radio"></span> No <span class="radio"></span></div>
        <div class="rule"></div>
        <p class="q">Do you currently smoke?</p>
        <div class="answer">Yes <span class="radio"></span> No <span class="radio"></span></div>
        <div class="rule"></div>
      </div>
    </div>
    <p class="declare">The information that I have provided is to the best of my knowledge correct. It is my responsibility to inform of any changes in my medical status.</p>
    <p class="sign">Patient/Parent/Person Responsible Signature: ______________________</p>
  </section>

  <section class="form form--details">
    <p class="form__doctors">Dr. Stefan Koralis &amp; Dr. Henry Ashford<br>Dental Surgeons</p>
    <p class="form__welcome">Welcome To Our Practice!</p>
    <p class="form__intro">This information is confidential and is necessary to enable us to offer you The Best Possible Care. We respect and protect the privacy of our patients and as such will only use details relevant to the treatment we may need to provide you. Thank you.</p>
    <div class="band">Patient Information</div>
    <div class="info-table info-table--fill">
      <div class="title">Ms <span class="radio radio--line"></span> Mrs <span class="radio radio--line"></span> Miss <span class="radio radio--line"></span> Mr <span class="radio radio--line"></span> Master <span class="radio radio--line"></span> Dr <span class="radio radio--line"></span> Other <span class="radio radio--line"></span></div>
      <div class="row"><span>Surname</span><span></span></div>
      <div class="row"><span>First Name</span><span></span></div>
      <div class="row"><span>Preferred</span><span></span></div>
      <div class="row"><span>Date of Birth</span><span></span></div>
      <div class="row"><span>Current Residential Address</span><span>Postcode:</span></div>
      <div class="row"><span>Postal Residential Address (if different)</span><span>Postcode:</span></div>
      <div class="row"><span>Occupation</span><span></span></div>
      <div class="row"><span>Employer</span><span></span></div>
    </div>
    <div class="band">Other Information</div>
    <p>Person responsible for your account (if yourself, please tick this) <span class="radio radio--line"></span></p>
    <div class="plain-fields">
      <div class="field">Name <i></i></div>
      <div class="field">Phone <i></i></div>
      <div class="field">Address <i></i></div>
    </div>
    <p class="insurance">Do you have Private Health Insurance? Yes <span class="radio radio--line"></span> No <span class="radio radio--line"></span><br>If yes, please specify the name (e.g. MedSure)</p>
    <div class="plain-fields">
      <div class="field">Name <i></i></div>
      <div class="field">Patient number <i></i></div>
    </div>
    <p class="note">Please note: If you are claiming please ensure that you have the card as it is required at time of treatment.</p>
  </section>

  <section class="form form--update">
    <div class="form__head">
      <p class="form__doctors">Dr. Henry Ashford &amp; Dr. Stefan Koralis<br>Dental Surgeons</p>
      <div class="form__name">Corvina Dental</div>
    </div>
    <p class="form__welcome">Welcome back To Our Practice!</p>
    <p class="form__intro">This information is confidential and is necessary to enable us to offer you The Best Possible Care. Because we haven't seen you in some time and because we care about your health status, please take your time and thoroughly complete the following update of your personal and medical information. It is essential that we know about your past and present medical history. Many medical conditions may interfere with dental procedures.</p>
    <div class="split">
      <div>
        <div class="band band--sky">Patient Information</div>
        <div class="info-table">
          <div class="title">Ms <span class="radio radio--line"></span> Mrs <span class="radio radio--line"></span> Miss <span class="radio radio--line"></span> Mr <span class="radio radio--line"></span> Master <span class="radio radio--line"></span> Dr <span class="radio radio--line"></span> Other <span class="radio radio--line"></span></div>
          <div class="row"><span>Surname</span><span></span></div>
          <div class="row"><span>First Name</span><span></span></div>
          <div class="row"><span>Preferred</span><span></span></div>
          <div class="row"><span>Date of Birth</span><span></span></div>
          <div class="row"><span>Current Residential Address</span><span>Postcode:</span></div>
          <div class="row"><span>Postal Residential Address (if different)</span><span>Postcode:</span></div>
          <div class="row"><span>Occupation</span><span></span></div>
          <div class="row"><span>Employer</span><span></span></div>
        </div>
      </div>
      <div>
        <div class="band band--sky">Patient Contact Information</div>
        <div class="info-table">
          <div class="row"><span>Phone</span><span>M:<br>H:<br>W:</span></div>
          <div class="row"><span>Email</span><span></span></div>
          <div class="row"><span>Preferred</span><span></span></div>
          <div class="title title--ruled">Preferred method of communication:<br>SMS <span class="radio radio--line"></span> Phone <span class="radio radio--line"></span> Email <span class="radio radio--line"></span> Mail <span class="radio radio--line"></span> Referred by:</div>
        </div>
        <div class="band band--sky band--bright">Emergency Contact</div>
        <div class="info-table">
          <div class="row"><span>Name</span><span></span></div>
          <div class="row"><span>Relationship</span><span></span></div>
          <div class="row"><span>Contact Number</span><span></span></div>
        </div>
      </div>
    </div>
    <p class="q">Have you taken any prescribed medication or dietary supplements in the last 12 months? (If yes, please list below)</p>
    <div class="answer">Yes <span class="radio radio--line"></span> No <span class="radio radio--line"></span></div>
    <p class="q">Has anybody in your family history ever suffered from heart problems? (Please give details below)</p>
    <div class="answer">Yes <span class="radio radio--line"></span> No <span class="radio radio--line"></span></div>
    <p class="q">Have you ever had or are you suffering from any of the following? Please tick any that apply:</p>
    <ul class="conditions conditions--three">
      <li><span class="radio radio--line"></span>Rheumatic fever</li><li><span class="radio radio--line"></span>Kidney Disease</li><li><span class="radio radio--line"></span>High cholesterol</li>
      <li><span class="radio radio--line"></span>Epilepsy</li><li><span class="radio radio--line"></span>Heart Attack</li><li><span class="radio radio--line"></span>Cancer</li>
      <li><span class="radio radio--line"></span>Asthma</li><li><span class="radio radio--line"></span>High Blood Pressure</li><li><span class="radio radio--line"></span>Pace-maker</li>
      <li><span class="radio radio--line"></span>Tuberculosis</li><li><span class="radio radio--line"></span>Bleeding problems</li><li><span class="radio radio--line"></span>Osteoporosis</li>
      <li><span class="radio radio--line"></span>Radiation Therapy</li><li><span class="radio radio--line"></span>Artificial joints</li><li><span class="radio radio--line"></span>Heart rate problems</li>
      <li><span class="radio radio--line"></span>Dizziness, fainting</li><li><span class="radio radio--line"></span>Respiratory problems</li><li><span class="radio radio--line"></span>Heart murmur</li>
      <li><span class="radio radio--line"></span>Hepatitis A B or C</li><li><span class="radio radio--line"></span>HIV Positive</li><li></li>
      <li><span class="radio radio--line"></span>Diabetes</li>
    </ul>
  </section>

</div>
</body>
</html>
```